Business Cards - New Logo Rebranding

Hello We know have a red and blue logo and are looking to create new cards. We are looking for the best creativity of the new logo merged with some of the existing artwork provided.

Target Market(s)

Realtors

Industry/Entity Type

Real Estate

Contact Information for Business Card

New logo with rebranded colors

Requirements
Must have
• Creative use of the new logo

```html
<!DOCTYPE html>
<html lang="en">
<head>
<meta charset="utf-8">
<title>Norvale Group – Business Cards</title>
<link href="https://fonts.googleapis.com/css2?family=Roboto:wght@400;500;700&display=swap" rel="stylesheet">
<style>
  :root {
    --bg: #3a3a3a;
    --brand-blue: #0a6ebd;
    --brand-red: #e03a3e;
    --ink: #555;
    --rule: #ccc;
    --paper: #ffffff;
    --faint-blue: rgba(10,110,189,0.06);
  }
  * { margin: 0; padding: 0; box-sizing: border-box; }
  html, body { width: 1200px; height: 689px; overflow: hidden; }
  body {
    background: var(--bg);
    font-family: "Roboto", Arial, sans-serif;
    position: relative;
  }
  .card {
    position: absolute;
    top: 190px;
    width: 540px;
    height: 310px;
    border-radius: 22px;
    overflow: hidden;
  }

  /* Back */
  .card-back { left: 35px; background: var(--brand-blue); }
  .back-mark {
    position: absolute; left: 0; right: 0; top: 84px;
    display: flex; align-items: center; justify-content: center; gap: 16px;
    white-space: nowrap;
  }
  .back-mark .dot {
    flex: 0 0 auto;
    width: 60px; height: 60px; border-radius: 50%; border: 5px solid var(--paper);
  }
  .back-mark .name {
    color: var(--paper); font-weight: 700; font-size: 36px; letter-spacing: 1px;
  }
  .services {
    position: absolute; left: 0; right: 0; bottom: 46px; text-align: center;
    color: var(--paper); font-size: 15px; letter-spacing: 0.5px; white-space: nowrap;
  }

  /* Front */
  .card-front { left: 625px; background: var(--paper); }
  .front-deco {
    position: absolute; left: 70px; top: 40px; width: 300px; height: 300px;
    border-radius: 50%; background: var(--faint-blue);
  }
  .brand { position: absolute; right: 34px; top: 32px; text-align: right; }
  .brand-row {
    display: flex; align-items: center; gap: 12px; justify-content: flex-end;
    white-space: nowrap;
  }
  .brand-row .dot { flex: 0 0 auto; width: 50px; height: 50px; border-radius: 50%; background: var(--brand-red); }
  .brand-row .name { color: var(--brand-blue); font-weight: 700; font-size: 28px; letter-spacing: 1px; }
  .brand .tagline {
    margin-top: 4px; font-size: 8px; color: var(--brand-blue); letter-spacing: 1px;
  }
  .contact-web {
    position: absolute; right: 34px; top: 128px; width: 260px;
    border-top: 1px solid var(--rule); padding-top: 10px;
    font-size: 13px; color: var(--ink); line-height: 1.5; text-align: right;
    white-space: nowrap;
  }
  .person { position: absolute; left: 34px; top: 168px; }
  .person .full-name { color: var(--brand-blue); font-size: 24px; font-weight: 500; }
  .person .role {
    color: var(--brand-red); font-size: 14px; padding-bottom: 8px;
    border-bottom: 1px solid var(--rule); width: 200px;
  }
  .phones { margin-top: 8px; font-size: 14px; color: var(--ink); line-height: 1.45; }
  .phones div { display: flex; align-items: center; gap: 8px; }
  .phones svg { width: 12px; height: 12px; fill: var(--brand-blue); }
  .stripe-red { position: absolute; left: 0; right: 0; bottom: 18px; height: 3px; background: var(--brand-red); }
  .stripe-blue { position: absolute; left: 0; right: 0; bottom: 0; height: 14px; background: var(--brand-blue); }
</style>
</head>
<body>
  <section class="card card-back">
    <div class="back-mark"><span class="dot"></span><span class="name">NORVALE GROUP</span></div>
    <p class="services">HOME • SEWER • MOLD • COMMERCIAL • TERMITE • ROOF</p>
  </section>

  <section class="card card-front">
    <div class="front-deco"></div>
    <div class="brand">
      <div class="brand-row"><span class="dot"></span><span class="name">NORVALE GROUP</span></div>
      <div class="tagline">INSPECTION PROFESSIONALS</div>
    </div>
    <div class="contact-web">
      <div>danielmoreno@norvaleinspect.com</div>
      <div>www.NorvaleInspect.com</div>
    </div>
    <div class="person">
      <div class="full-name">Daniel Moreno</div>
      <div class="role">Certified Mold Inspector</div>
      <div class="phones">
        <div><svg viewBox="0 0 24 24"><path d="M6.6 10.8a15 15 0 0 0 6.6 6.6l2.2-2.2a1 1 0 0 1 1-.25 11.4 11.4 0 0 0 3.6.57 1 1 0 0 1 1 1V20a1 1 0 0 1-1 1A17 17 0 0 1 3 4a1 1 0 0 1 1-1h3.5a1 1 0 0 1 1 1c0 1.250.2 2.45.57 3.57a1 1 0 0 1-.25 1z"/></svg>800.555.0142</div>
        <div><svg viewBox="0 0 24 24"><path d="M7 1h10a2 2 0 0 1 2 2v18a2 2 0 0 1-2 2H7a2 2 0 0 1-2-2V3a2 2 0 0 1 2-2zm0 3v14h10V4z"/></svg>562.555.0187</div>
      </div>
    </div>
    <div class="stripe-red"></div>
    <div class="stripe-blue"></div>
  </section>
</body>
</html>
```